Tellmora Corporate Stationery

Look for design of all new corporate stationery for an existing insurance broking business that is going through a redesign and move from older partners to younger family members. New Logo is attached. Company is Brisbane based.
Colours in the Logo is Hex #43bed8 and website features a lot of hex #17b8d8. Website front page "A plan to protect you" - headline. "Professional and Individual advice to protect your greatest assets" - tagline.

Stationery required: Business Cards, Letter head, Thank-you cards, Birthday cards, Presentation folders, With Compliment slips and a powerpoint template. We also would like to send a card to all customers with the something along of the lines of "something new".

Target Market(s)

Customers of Insurance business looking at superannuation, life and income protection insurance, investment advice and wills

Industry/Entity Type

Insurance Broker

Font styles to use
Other font styles liked:
• same as logo

Requirements
Must have
• The above designs for new stationery for the new business including:
• Business Cards, Letter head, Thank-you cards, Birthday cards, Presentation folders, With Compliment slips and a powerpoint template. We also would like to send a card to all customers with the something along of the lines of "something new".
Nice to have
• It is a new look - long time family business being passed to next generation - big focus on advice for YOU, individual advice etc..

```html
<!DOCTYPE html>
<html lang="en">
<head>
<meta charset="utf-8">
<title>Tellmora Corporate Stationery</title>
<link rel="stylesheet" href="https://fonts.googleapis.com/css2?family=Oswald:wght@400;500&family=Open+Sans:wght@400;600&family=Quicksand:wght@300;400&display=swap">
<style>
  :root{
    --teal:#43bed8;
    --teal-bright:#17b8d8;
    --grey:#7a7a7c;
    --grey-dark:#474749;
    --ink:#5a5a5c;
    --paper:#ffffff;
    --slide:#ececec;
    --canvas:#e9e9ea;
    --rule:#c8c8c8;
  }
  *{box-sizing:border-box;margin:0;padding:0}
  html,body{width:1028px;height:1200px;overflow:hidden;background:var(--canvas)}
  body{position:relative;font-family:"Open Sans",sans-serif;color:var(--ink)}
  .item{position:absolute;background:var(--paper);overflow:hidden}

  /* brand name */
  .brand{display:flex;align-items:center;gap:4px;font-family:"Oswald",sans-serif;font-weight:500;color:var(--teal);letter-spacing:.12em;text-transform:uppercase;line-height:1}
  .brand .dot{border-radius:50%;background:var(--teal);flex:none}
  .brand.white{color:#fff}
  .brand.white .dot{background:#fff}

  .faint-circle{position:absolute;border-radius:50%;border:16px solid rgba(0,0,0,.045)}
  .faint-circle.light{border-color:rgba(255,255,255,.1)}

  .base-band{position:absolute;left:0;right:0;bottom:0;height:5px;display:flex}
  .base-band .t{background:var(--teal);flex:0 0 77%}
  .base-band .g{background:var(--grey);flex:1}

  .contact{font-size:4.3px;line-height:6.2px;color:var(--ink)}
  .contact .name{color:var(--teal);font-weight:600;font-size:5px}

  /* letterhead */
  .letterhead{left:217px;top:94px;width:280px;height:396px}
  .letterhead .brand{position:absolute;left:24px;top:44px;font-size:10px}
  .letterhead .brand .dot{width:9px;height:9px}
  .letterhead .contact{position:absolute;left:207px;top:18px}

  /* folder */
  .folder{left:544px;top:76px;width:332px;height:418px;background:var(--teal)}
  .folder .spine{position:absolute;left:6px;top:0;bottom:0;width:1px;background:rgba(0,0,0,.08)}
  .folder .brand{position:absolute;left:0;right:0;top:196px;justify-content:center;font-size:26px;gap:10px}
  .folder .brand .dot{width:22px;height:22px}

  /* business cards */
  .card{left:116px;width:126px;height:70px}
  .card-back{top:526px}
  .card-back .brand{position:absolute;left:10px;top:29px;font-size:7px;gap:3px}
  .card-back .brand .dot{width:6px;height:6px}
  .card-back .contact{position:absolute;left:72px;top:10px;font-size:3.2px;line-height:4.6px}
  .card-back .contact .name{font-size:4.2px}
  .card-back .base-band{height:3px}
  .card-front{top:618px;background:var(--teal)}
  .card-front .brand{position:absolute;left:0;right:0;top:29px;justify-content:center;font-size:9px;gap:5px}
  .card-front .brand .dot{width:8px;height:8px}

  /* compliment slip */
  .slip{left:275px;top:535px;width:313px;height:150px}
  .slip .brand{position:absolute;left:15px;top:23px;font-size:9px}
  .slip .brand .dot{width:8px;height:8px}
  .slip .contact{position:absolute;left:15px;top:44px;font-size:4.6px}

  /* envelope */
  .envelope{left:618px;top:536px;width:313px;height:150px}
  .envelope svg{position:absolute;left:0;top:0}
  .envelope .brand{position:absolute;left:0;right:0;top:16px;justify-content:center;font-size:7px;gap:3px}
  .envelope .brand .dot{width:6px;height:6px}
  .envelope .web{position:absolute;left:0;right:0;top:29px;text-align:center;font-size:3.8px;color:#fff}

  /* slides */
  .slide{width:257px;height:193px;background:var(--slide)}
  .col1{left:102px}.col2{left:383px}.col3{left:670px}
  .row1{top:733px}.row2{top:938px}
  .slide-head{position:absolute;left:14px;right:14px;top:13px;border-bottom:1px solid var(--rule);padding-bottom:1px}
  .slide-head h2{font-family:"Oswald",sans-serif;font-weight:400;font-size:11px;color:var(--teal);line-height:1.1}
  .slide-head p{font-size:5.5px;color:var(--grey)}
  .slide-head .dot{position:absolute;right:4px;top:3px;width:10px;height:10px;border-radius:50%;background:var(--grey)}
  .small{font-size:3.4px;line-height:4.6px;color:var(--ink)}

  .title-slide .brand{position:absolute;left:0;right:0;top:68px;justify-content:center;font-size:18px;gap:8px}
  .title-slide .brand .dot{width:16px;height:16px}
  .title-slide .lines{position:absolute;left:0;right:0;top:118px;text-align:center;font-family:"Oswald",sans-serif;font-size:14px;line-height:18px;color:var(--grey)}
  .title-slide .lines strong{color:var(--teal);font-weight:500;font-size:15px;display:block}

  .team{position:absolute;left:18px;right:18px;top:54px;display:flex;justify-content:space-between}
  .member{width:52px}
  .photo{width:52px;height:50px;background:var(--grey-dark);border:1px solid #333;display:flex;align-items:center;justify-content:center;font-size:6px;color:#ddd}
  .member h3{font-size:5px;font-weight:400;color:var(--teal);margin-top:22px}
  .member .role{font-size:4.6px;color:var(--grey);margin-bottom:5px}

  .groups{position:absolute;left:16px;right:16px;top:57px;display:grid;grid-template-columns:1fr 1fr;column-gap:10px;row-gap:12px}
  .groups h3{font-size:5.5px;font-weight:400;color:var(--teal);margin-bottom:3px}

  .bars{position:absolute;left:24px;top:50px}
  .bar-copy{position:absolute;left:154px;top:58px;width:90px}
  .bar-foot{position:absolute;left:20px;right:20px;top:146px}

  .pie-copy{position:absolute;left:20px;top:62px;width:110px;text-align:center}
  .pie{position:absolute;left:158px;top:54px}
  .legend{position:absolute;left:158px;top:122px;width:74px}
  .legend div{display:flex;align-items:center;gap:3px;font-size:3.4px;border-bottom:1px solid var(--rule);padding:1px 0}
  .legend span{width:5px;height:5px;flex:none}
  .pie-foot{position:absolute;left:158px;top:150px;width:78px}

  .thanks{left:670px;top:938px;background:var(--teal-bright)}
  .thanks h2{position:absolute;left:0;right:0;top:68px;text-align:center;font-family:"Quicksand",sans-serif;font-weight:300;color:#fff;font-size:40px;line-height:1}
  .thanks h2 small{display:block;font-size:22px;margin-top:2px}
  .thanks .contact{position:absolute;left:0;right:0;top:160px;text-align:center;color:#fff;font-size:4px;line-height:5.4px}
</style>
</head>
<body>

<!-- Letterhead -->
<section class="item letterhead">
  <div class="faint-circle" style="left:64px;top:150px;width:180px;height:180px"></div>
  <div class="brand"><span class="dot"></span>Tellmora</div>
  <div class="contact">
    214 Harbour Street<br>Brisbane QLD 4000<br>
    &#9742; 07 3100 4712<br>&#9742; 07 3100 6085<br>&#9742; 07 3100 5293<br>
    &#9993; hello@tellmora-mail.com<br>&#9679; www.tellmora-group.com
  </div>
  <div class="base-band"><span class="t"></span><span class="g"></span></div>
</section>

<!-- Presentation folder -->
<section class="item folder">
  <div class="faint-circle light" style="left:20px;top:40px;width:300px;height:300px;border-width:28px"></div>
  <div class="spine"></div>
  <div class="brand white"><span class="dot"></span>Tellmora</div>
</section>

<!-- Business card, back -->
<section class="item card card-back">
  <div class="brand"><span class="dot"></span>Tellmora</div>
  <div class="contact">
    <span class="name">ALEX CARTER</span><br>CEO / FOUNDER<br>
    214 Harbour Street<br>Brisbane QLD 4000<br>
    07 3100 4712<br>07 3100 6085<br>hello@tellmora-mail.com<br>www.tellmora-group.com
  </div>
  <div class="base-band"><span class="t"></span><span class="g"></span></div>
</section>

<!-- Business card, front -->
<section class="item card card-front">
  <div class="brand white"><span class="dot"></span>Tellmora</div>
</section>

<!-- With compliments slip -->
<section class="item slip">
  <div class="faint-circle" style="left:180px;top:20px;width:110px;height:110px;border-width:12px"></div>
  <div class="brand"><span class="dot"></span>Tellmora</div>
  <div class="contact">214 Harbour Street<br>Brisbane QLD 4000</div>
  <div class="base-band"><span class="t"></span><span class="g"></span></div>
</section>

<!-- Envelope -->
<section class="item envelope">
  <svg width="313" height="150" viewBox="0 0 313 150" aria-hidden="true">
    <path d="M0 0H313V10L300 58H13L0 10Z" fill="var(--teal)"/>
  </svg>
  <div class="brand white"><span class="dot"></span>Tellmora</div>
  <div class="web">www.tellmora-group.com</div>
</section>

<!-- Slide: title -->
<section class="item slide title-slide col1 row1">
  <div class="brand"><span class="dot"></span>Tellmora</div>
  <div class="lines">Welcome to Our<strong>Presentation Name</strong>Description</div>
  <div class="base-band"><span class="t"></span><span class="g"></span></div>
</section>

<!-- Slide: team -->
<section class="item slide col2 row1">
  <header class="slide-head"><h2>Heading Here</h2><p>Sub Heading</p><span class="dot"></span></header>
  <div class="team">
    <div class="member"><div class="photo" role="img" aria-label="Team member portrait">Photo</div><h3>Team member1</h3><p class="role">Title</p><p class="small">Leads the firm and guides each plan with care.</p></div>
    <div class="member"><div class="photo" role="img" aria-label="Team member portrait">Photo</div><h3>Team member2</h3><p class="role">Title</p><p class="small">Helps families set up cover that fits their lives.</p></div>
    <div class="member"><div class="photo" role="img" aria-label="Team member portrait">Photo</div><h3>Team member3</h3><p class="role">Title</p><p class="small">Looks after super, savings and long term goals.</p></div>
    <div class="member"><div class="photo" role="img" aria-label="Team member portrait">Photo</div><h3>Team member4</h3><p class="role">Title</p><p class="small">Keeps every policy clear, current and easy to read.</p></div>
  </div>
</section>

<!-- Slide: groups -->
<section class="item slide col3 row1">
  <header class="slide-head"><h2>Heading Here</h2><p>Sub Heading</p><span class="dot"></span></header>
  <div class="groups">
    <div><h3>Group1</h3><p class="small">Clear advice on cover, savings and plans that suit the way you live and work.</p></div>
    <div><h3>Group4</h3><p class="small">Clear advice on cover, savings and plans that suit the way you live and work.</p></div>
    <div><h3>Group2</h3><p class="small">Clear advice on cover, savings and plans that suit the way you live and work.</p></div>
    <div><h3>Group5</h3><p class="small">Clear advice on cover, savings and plans that suit the way you live and work.</p></div>
    <div><h3>Group3</h3><p class="small">Clear advice on cover, savings and plans that suit the way you live and work.</p></div>
    <div><h3>Group6</h3><p class="small">Clear advice on cover, savings and plans that suit the way you live and work.</p></div>
  </div>
</section>

<!-- Slide: bar chart -->
<section class="item slide col1 row2">
  <header class="slide-head"><h2>Heading Here</h2><p>Sub Heading</p><span class="dot"></span></header>
  <svg class="bars" width="110" height="80" viewBox="0 0 110 80" role="img" aria-label="Bar chart with four values">
    <g stroke="#d0d0d0" stroke-width=".5">
      <line x1="0" y1="8" x2="104" y2="8"/><line x1="0" y1="18" x2="104" y2="18"/><line x1="0" y1="28" x2="104" y2="28"/>
      <line x1="0" y1="38" x2="104" y2="38"/><line x1="0" y1="48" x2="104" y2="48"/><line x1="0" y1="58" x2="104" y2="58"/>
      <line x1="0" y1="68" x2="104" y2="68"/><line x1="0" y1="78" x2="104" y2="78"/>
    </g>
    <g fill="var(--teal)">
      <rect x="26" y="0" width="12" height="78"/><rect x="42" y="10" width="12" height="68"/>
      <rect x="58" y="30" width="12" height="48"/><rect x="74" y="18" width="12" height="60"/>
    </g>
    <g fill="#fff" font-size="3.4" font-family="Open Sans, sans-serif">
      <text transform="translate(34 76) rotate(-90)">Sub text1</text><text transform="translate(50 76) rotate(-90)">Sub text2</text>
      <text transform="translate(66 76) rotate(-90)">Sub text3</text><text transform="translate(82 76) rotate(-90)">Sub text4</text>
    </g>
  </svg>
  <p class="small bar-copy">We look at your whole picture before we suggest any cover. Each plan is built for you, checked each year and kept simple. Cover, super and savings work better together when one team looks after them.</p>
  <p class="small bar-foot">Our advice covers life and income protection, superannuation, investments and wills. We meet you, listen first and then build a plan that protects your greatest assets for the years ahead.</p>
</section>

<!-- Slide: pie chart -->
<section class="item slide col2 row2">
  <header class="slide-head"><h2>Heading Here</h2><p>Sub Heading</p><span class="dot"></span></header>
  <p class="small pie-copy">Most of our clients come to us for life and income protection. The rest of our work is spread across super, investment advice and estate planning, so every part of your plan is reviewed by one trusted team.<br><br>Each review is free for existing clients and takes less than an hour of your time.</p>
  <svg class="pie" width="60" height="60" viewBox="-30 -30 60 60" role="img" aria-label="Pie chart of client services">
    <path d="M0 0L0 -28A28 28 0 1 1 -24.2 14Z" fill="var(--teal)" transform="rotate(150)"/>
    <path d="M0 0L5 -27.6A28 28 0 0 1 26.6 -8.6Z" fill="var(--grey)"/>
    <path d="M0 0L26.6 -8.6A28 28 0 0 1 27 7.5Z" fill="var(--teal)"/>
    <path d="M0 0L27 7.5A28 28 0 0 1 12 25.3Z" fill="var(--grey)"/>
    <g stroke="#fff" stroke-width=".8"><line x1="0" y1="0" x2="5" y2="-27.6"/><line x1="0" y1="0" x2="26.6" y2="-8.6"/><line x1="0" y1="0" x2="27" y2="7.5"/><line x1="0" y1="0" x2="12" y2="25.3"/></g>
  </svg>
  <div class="legend">
    <div><span style="background:var(--teal)"></span>Life and income cover 50%</div>
    <div><span style="background:var(--grey)"></span>Super and investments 30%</div>
  </div>
  <p class="small pie-foot">Figures based on client files for the past year.</p>
</section>

<!-- Slide: thanks -->
<section class="item slide thanks">
  <div class="faint-circle light" style="left:80px;top:20px;width:150px;height:150px;border-width:16px"></div>
  <h2>Thanks<small>For Coming</small></h2>
  <div class="contact">214 Harbour Street, Brisbane QLD 4000<br>P: 07 3100 4712 M: 07 3100 6085 F: 07 3100 5293<br>hello@tellmora-mail.com | www.tellmora-group.com</div>
</section>

</body>
</html>
```